Brochure for real estate company

We need the brochure in the attachement re-designed in a consistent way with our website. The text and the structure of the text should not be altered, but addidtional design-elements and other stuff can be added. We're looking for a simple and catchy design as in our website (www.falkner-wohnbau.ch). We need design propositions in file formats where we can always change the text ourselves if that is neccessary later on.

Industry/Entity Type

Real Estate

Font styles to use
Sans Serif

Colors
ec2027
f04a50

```html
<!DOCTYPE html>
<html lang="de">
<head>
<meta charset="utf-8">
<title>Klartext – Broschüre</title>
<link rel="stylesheet" href="https://fonts.googleapis.com/css2?family=Arvo&family=Noto+Sans:wght@400&display=swap">
<style>
  :root {
    --brand-red: #ec2027;
    --panel-red: #f04a50;
    --ink: #1e1e1e;
    --paper: #e0e0df;
    --frame: #c4c4c4;
    --white: #ffffff;
  }
  html, body {
    margin: 0;
    padding: 0;
    overflow: hidden;
  }
  .page {
    position: relative;
    width: 899px;
    height: 1200px;
    box-sizing: border-box;
    background: var(--paper);
    border: 2px solid var(--frame);
    overflow: hidden;
  }
  .rule {
    position: absolute;
    top: 155px;
    height: 14px;
  }
  .rule--red { left: 2px; width: 342px; background: var(--brand-red); }
  .rule--dark { left: 351px; width: 546px; background: var(--ink); }
  .hero-photo {
    position: absolute;
    left: 2px;
    top: 173px;
    width: 443px;
    height: 396px;
    background: linear-gradient(135deg, #e9e7e3 0%, #cfcac2 45%, #b49a6a 70%, #8a7248 100%);
  }
  .headline-panel {
    position: absolute;
    left: 448px;
    top: 173px;
    width: 449px;
    height: 396px;
    background: var(--panel-red);
  }
  .headline-panel .notch {
    position: absolute;
    left: -14px;
    top: 356px;
    transform: translateY(-150%);
  }
  .headline {
    position: absolute;
    left: 35px;
    top: 117px;
    margin: 0;
    font-family: "Arvo", serif;
    font-weight: 400;
    font-size: 20px;
    line-height: 36px;
    color: var(--white);
  }
  .benefits {
    position: absolute;
    left: 55px;
    top: 628px;
    width: 780px;
    margin: 0;
    padding: 0;
    list-style: none;
  }
  .benefit {
    position: relative;
    padding-left: 42px;
    margin-bottom: 60px;
    font-family: "Noto Sans", sans-serif;
    font-size: 16.5px;
    line-height: 30px;
    color: var(--ink);
  }
  .benefit-icon {
    position: absolute;
    left: 0;
    top: 5px;
  }
</style>
</head>
<body>
<div class="page">
  <div class="rule rule--red"></div>
  <div class="rule rule--dark"></div>

  <div class="hero-photo" role="img" aria-label="Foto eines antiken Messingschlüssels und einer Taschenuhr auf einer Zeitungsseite mit dem Wort Investing"></div>

  <div class="headline-panel">
    <svg class="notch" width="16" height="40" viewBox="0 0 16 40" aria-hidden="true">
      <path d="M16 0 L16 40 L2 22 Q0 20 2 18 Z" fill="var(--panel-red)"/>
    </svg>
    <h1 class="headline">Klartext: Das machen wir<br>besser als die Konkurrenz<br>Wir sparen nicht auf Ihre<br>Kosten:</h1>
  </div>

  <ul class="benefits">
    <li class="benefit">
      <svg class="benefit-icon" width="38" height="16" viewBox="0 0 38 16" aria-hidden="true">
        <circle cx="8" cy="8" r="6" fill="none" stroke="var(--brand-red)" stroke-width="2.2"/>
        <path d="M14 5 H28 V1 L37 8 L28 15 V11 H14 Z" fill="var(--brand-red)"/>
      </svg>
      Viele Vermittler inserieren Objekte mit nur einem oder maximal zwei Bildern auf den<br>Immobilienplattformen. Resultat: Weniger Kosten für den Vermittler, weniger<br>Interessenten für den Verkäufer - nicht bei uns!
    </li>
    <li class="benefit">
      <svg class="benefit-icon" width="38" height="16" viewBox="0 0 38 16" aria-hidden="true">
        <circle cx="8" cy="8" r="6" fill="none" stroke="var(--brand-red)" stroke-width="2.2"/>
        <path d="M14 5 H28 V1 L37 8 L28 15 V11 H14 Z" fill="var(--brand-red)"/>
      </svg>
      Wir verkaufen nur für Sie: Grosse Vermittler wollen Objekte verkaufen, gleich welches.<br>Aus diesem Grund werden Interessenten dort immer (teilweise sogar automatisiert per E-<br>Mail) Vergleichsobjekte präsentiert, was die Chance verringert, ihm Ihr Objekt<br>näherzubringen - bei uns sind Sie und Ihre Liegenschaft im Mittelpunkt.
    </li>
    <li class="benefit">
      <svg class="benefit-icon" width="38" height="16" viewBox="0 0 38 16" aria-hidden="true">
        <circle cx="8" cy="8" r="6" fill="none" stroke="var(--brand-red)" stroke-width="2.2"/>
        <path d="M14 5 H28 V1 L37 8 L28 15 V11 H14 Z" fill="var(--brand-red)"/>
      </svg>
      Wir nehmen uns Zeit: Grosse Vermittler arbeiten oft mit computergenerierten<br>Standarddokumentationen, die sich auf maximal 2 Seiten beschränken. Wir rücken Ihre<br>Liegenschaft durch eine individualisierte Dokumentation ins richtige Licht.
    </li>
  </ul>
</div>
</body>
</html>
```